Home Remodeling company needs a business card design

we need a business card design for home remodeling company in hamilton county, indiana USA. we offers a wide range of construction services including whole house renovations, Design and Build Basements and Kitchen and Bathroom Remodeling . we would like to see designs for both site of business card that use the same color of the company logo and also including all information below :
1- Karim Feltous CEO / General Contractor
2- all company contacts Telephone numbers ( 1-888-DULOM-47 ) ( 317-555-0193) email address ( info@dulomhome.com) website ( www.dulomhome.com ) and social media logos (Facebook- twitter- google plus )
3- company logo
4- licensed . insured . bonded

```html
<!DOCTYPE html>
<html lang="en">
<head>
<meta charset="utf-8">
<title>Dulom Home Remodeling – Business Card</title>
<link href="https://fonts.googleapis.com/css2?family=Open+Sans:wght@400;600;800&family=Crimson+Text:wght@600&display=swap" rel="stylesheet">
<style>
  :root {
    --brand-red: #c8323a;
    --brand-charcoal: #3a3a3c;
    --tagline-grey: #6e6e70;
    --text-dark: #222222;
    --card-white: #ffffff;
    --page-bg: #e9e7e4;
    --social-one: #d8432f;
    --social-two: #3b5ea8;
    --social-three: #2fb2e6;
  }
  * { margin: 0; padding: 0; box-sizing: border-box; }
  html, body { width: 1189px; height: 1200px; overflow: hidden; background: var(--page-bg); }
  .card {
    position: absolute;
    width: 1123px; height: 642px;
    background: var(--card-white);
    transform: scale(0.816);
    transform-origin: top left;
    overflow: hidden;
    font-family: "Open Sans", Arial, sans-serif;
    box-shadow: 0 4px 14px rgba(0,0,0,0.18);
  }
  .card--front { left: 140px; top: 45px; }
  .card--back { left: 140px; top: 623px; }

  .brand { position: absolute; }
  .brand__name {
    font-weight: 800; color: var(--brand-charcoal);
    font-size: 118px; line-height: 1; letter-spacing: 4px;
  }
  .brand__tagline {
    margin-top: 4px;
    font-weight: 600; color: var(--tagline-grey);
    font-size: 36px; line-height: 1; letter-spacing: 17px; white-space: nowrap;
  }
  .card--front .brand { left: 70px; top: 46px; }
  .card--back .brand { left: 220px; top: 236px; }

  .person { position: absolute; right: 55px; top: 238px; text-align: right; }
  .person__name { font-family: "Crimson Text", Georgia, serif; font-weight: 600; font-size: 52px; color: var(--brand-red); line-height: 1.1; }
  .person__title { font-size: 34px; color: var(--text-dark); line-height: 1.3; }

  .contacts { position: absolute; left: 56px; top: 345px; list-style: none; }
  .contacts li { display: flex; align-items: center; height: 50px; font-size: 36px; color: var(--text-dark); }
  .contacts svg { width: 28px; height: 28px; margin-right: 24px; flex: none; }

  .swoosh { position: absolute; inset: 0; width: 1123px; height: 642px; }

  .social { position: absolute; right: 59px; top: 527px; display: flex; gap: 20px; }
  .social span { width: 78px; height: 78px; border-radius: 6px; display: block; }
  .social .s1 { background: var(--social-one); }
  .social .s2 { background: var(--social-two); }
  .social .s3 { background: var(--social-three); }

  .back-band {
    position: absolute; left: 0; bottom: 0; width: 100%; height: 92px;
    background: var(--brand-red);
    display: flex; align-items: center; justify-content: center;
    color: var(--card-white); font-weight: 600; font-size: 28px; letter-spacing: 8px;
  }
</style>
</head>
<body>

<section class="card card--front">
  <svg class="swoosh" viewBox="0 0 1123 642" aria-hidden="true">
    <path d="M0,593 Q600,640 1123,368 L1123,642 L0,642 Z" fill="var(--brand-red)"/>
    <path d="M0,540 Q620,600 1123,347 L1123,360 Q620,628 0,585 Z" fill="var(--brand-charcoal)"/>
  </svg>

  <div class="brand">
    <div class="brand__name">DULOM</div>
    <div class="brand__tagline">HOME REMODELING</div>
  </div>

  <div class="person">
    <div class="person__name">Karim Feltous</div>
    <div class="person__title">CEO / General Contractor</div>
  </div>

  <ul class="contacts">
    <li><svg viewBox="0 0 26 26"><rect width="26" height="26" fill="var(--brand-red)"/><path d="M8 5 L11 5 L12 9 L10 10.5 Q12 15 15.5 16.5 L17 14.5 L21 15.5 L21 19 Q14 21 9 15 Q5 10 8 5Z" fill="#fff"/></svg>1-888-DULOM-47</li>
    <li><svg viewBox="0 0 26 26"><rect width="26" height="26" fill="var(--brand-red)"/><path d="M8 5 L11 5 L12 9 L10 10.5 Q12 15 15.5 16.5 L17 14.5 L21 15.5 L21 19 Q14 21 9 15 Q5 10 8 5Z" fill="#fff"/></svg>317-555-0193</li>
    <li><svg viewBox="0 0 26 26"><rect width="26" height="26" fill="var(--brand-red)"/><rect x="4" y="7" width="18" height="12" fill="#fff"/><path d="M4 7 L13 14 L22 7" stroke="var(--brand-red)" stroke-width="1.6" fill="none"/></svg>info@dulomhome.com</li>
    <li><svg viewBox="0 0 26 26"><rect width="26" height="26" fill="var(--brand-red)"/><circle cx="13" cy="13" r="8" fill="none" stroke="#fff" stroke-width="2"/><path d="M5 13 H21 M13 5 Q8 13 13 21 M13 5 Q18 13 13 21" stroke="#fff" stroke-width="1.4" fill="none"/></svg>www.dulomhome.com</li>
  </ul>

  <div class="social" aria-label="Social media links">
    <span class="s1"></span><span class="s2"></span><span class="s3"></span>
  </div>
</section>

<section class="card card--back">
  <div class="brand">
    <div class="brand__name">DULOM</div>
    <div class="brand__tagline">HOME REMODELING</div>
  </div>
  <div class="back-band">LICENSED · INSURED · BONDED</div>
</section>

</body>
</html>
```